ORLA - Óptica Médica - web design and concept

Website concept - Create and develop our website design and structure. ORLA is an optical store chain, and we are looking to establish our web and digital concept. In attachment there are several pictures about our stores and our logo.

The website structure should be user friendly. Colors should be light and the design as simple and minimalist as possible. There are different variations of the logothat can be used, check the file.

The website will include optical collections and sun collections as an online store. Also, a medical menu should be considered in order for clients to schedule optometry appointments. There should also be a menu for client assistance where the clients can read about glass maintenance in our workshop.
Updates

Low design quality

Number of Pages Required

5+ page

Font styles to use
Serif
Sans Serif

Requirements
Must have
• Must be user-friendly and minimalist.
• Please USE PICTURES FROM THE BRANDS we sell: MERUN, BOSKA, PNW, KOLE, BAMPE
Nice to have
• Nice to inspire: ZEK glasses (see website https://ch.shopzek.com/en/)
• Nice to inspire: https://merun-eyewear.com/
• Nice to ispire: https://www.pnwglobe.com/en/
Should not have
• Hysteric colors and shapes

```html
<!DOCTYPE html>
<html lang="en">
<head>
<meta charset="utf-8">
<title>ORLA – Online Store</title>
<link rel="stylesheet" href="https://fonts.googleapis.com/css2?family=Poppins:wght@200;300;400;500;600&display=swap">
<style>
:root{
  --ink:#1c1c1c;
  --muted:#555;
  --accent:#e9b55a;
  --accent-deep:#d99d34;
  --line:#dcdcdc;
  --band:#f4f4f5;
  --white:#fff;
  --footer:#000;
  --footer-text:#e6e6e6;
}
*{margin:0;padding:0;box-sizing:border-box}
html,body{width:1200px;height:2715px;overflow:hidden;background:var(--white)}
body{position:relative;font-family:"Poppins",sans-serif;color:var(--ink)}
.abs{position:absolute}
.social{display:flex;gap:12px}
.social span{width:10px;height:10px;border-radius:50%;background:var(--ink);display:block}
.brand-mark{left:0;width:1200px;top:30px;text-align:center;font-size:26px;font-weight:400;letter-spacing:6px}
.topbar-item{top:14px;font-size:11px;display:flex;align-items:center;gap:7px}
.main-nav{top:104px;left:0;width:1200px;display:flex;justify-content:center;align-items:center;font-size:10px}
.main-nav a{color:var(--ink);text-decoration:none;margin-right:15px}
.main-nav a.is-active{color:var(--accent)}
.main-nav .cta{background:var(--accent);padding:4px 8px;margin-right:0;color:var(--ink)}
.page-title{top:256px;left:0;width:1200px;text-align:center;font-size:44px;font-weight:200}
.toolbar-label{top:478px;font-size:10px}
.select{top:473px;height:22px;border:1px solid var(--accent);font-size:10px;padding:3px 8px;display:flex;align-items:center}
.select::after{content:"";position:absolute;right:0;top:0;width:18px;height:20px;background:var(--accent)}
.select svg{position:absolute;right:5px;top:7px;z-index:1}
.view-icon{top:474px;width:22px;height:22px;display:grid;gap:2px}
.view-icon span{display:block}
.product{width:300px;text-align:center}
.product-photo{width:172px;height:86px;margin:0 auto;border-radius:40px 40px 46px 46px}
.product-name{margin-top:42px;font-size:17px;font-weight:300;color:#444}
.product-price{margin-top:4px;font-size:18px;font-weight:300}
.pagination{top:1786px;left:826px;display:flex;gap:11px;font-size:17px;font-weight:300;align-items:center}
.pagination .current{color:var(--accent)}
.feature{top:1884px;height:89px;width:286px;border:2px solid #e8e8e8;display:flex;align-items:center;padding-left:60px;gap:14px}
.feature h3{font-size:17px;font-weight:300;line-height:1}
.feature p{font-size:10px;margin-top:2px}
.brand-band{top:2009px;left:0;width:1200px;height:163px;background:var(--band)}
.partner{top:2070px;font-size:26px;font-weight:400;transform:translateX(-50%);white-space:nowrap;letter-spacing:1px}
.newsletter-title{top:2208px;left:0;width:1200px;text-align:center;font-size:25px;font-weight:300}
.newsletter-rule{top:2250px;left:538px;width:124px;height:1px;background:var(--accent)}
.email-field{top:2284px;left:302px;width:505px;height:71px;border:2px solid #e0e0e0;font-size:11px;padding:27px 30px;color:#444}
.email-submit{top:2284px;left:807px;width:91px;height:71px;background:var(--accent);display:flex;align-items:center;justify-content:center}
.site-footer{top:2393px;left:0;width:1200px;height:322px;background:var(--footer);color:var(--footer-text)}
.footer-logo{font-size:20px;letter-spacing:4px;color:var(--accent)}
.footer-about{font-size:11px;line-height:1.35;width:160px}
.footer-head{font-size:13px;font-weight:600;color:var(--accent)}
.footer-list{list-style:none;font-size:11px;line-height:16.5px}
.footer-list li::before{content:"";display:inline-block;width:3px;height:3px;border-radius:50%;background:var(--footer-text);margin:0 10px 2px 0}
.footer-rule{top:224px;left:161px;width:880px;height:1px;background:#666}
.footer-small{top:242px;font-size:11px}
</style>
</head>
<body>

<header>
  <div class="abs social" style="left:163px;top:17px">
    <span></span><span></span><span></span><span></span><span></span>
  </div>
  <div class="abs brand-mark">ORLA</div>
  <div class="abs topbar-item" style="left:820px">
    <svg width="10" height="11" viewBox="0 0 10 11"><rect x="1" y="4" width="8" height="7" fill="#1c1c1c"/><path d="M3 4V2.5a2 2 0 0 1 4 0V4" stroke="#1c1c1c" fill="none" stroke-width="1.3"/></svg>
    Your Cart &nbsp;( 0 )
  </div>
  <div class="abs topbar-item" style="left:937px">
    <svg width="11" height="11" viewBox="0 0 24 24"><path d="M6.6 10.8a15 15 0 0 0 6.6 6.6l2.2-2.2c.3-.3.7-.4 1-.2 1.1.4 2.3.6 3.6.6.6 0 1 .4 1 1V20c0 .6-.4 1-1 1A17 17 0 0 1 3 4c0-.6.4-1 1-1h3.5c.6 0 1 .4 1 1 0 1.3.2 2.5.6 3.6.1.3 0 .7-.2 1z" fill="#1c1c1c"/></svg>
    +015-482-730-6
  </div>
  <nav class="abs main-nav">
    <a href="#">Home</a>
    <a href="#" class="is-active">Online store</a>
    <a href="#">Company history</a>
    <a href="#">Medical section</a>
    <a href="#">Store</a>
    <a href="#">Contact Us</a>
    <a href="#" class="cta">Make an Appoinment</a>
  </nav>
</header>

<main>
  <h1 class="abs page-title">Online Store</h1>

  <div class="abs view-icon" style="left:160px;grid-template-columns:repeat(3,1fr)">
    <span style="background:var(--accent)"></span><span style="background:var(--accent)"></span><span style="background:var(--accent)"></span>
    <span style="background:var(--accent)"></span><span style="background:var(--accent)"></span><span style="background:var(--accent)"></span>
    <span style="background:var(--accent)"></span><span style="background:var(--accent)"></span><span style="background:var(--accent)"></span>
  </div>
  <div class="abs view-icon" style="left:203px;grid-template-columns:repeat(2,1fr)">
    <span style="background:var(--ink)"></span><span style="background:var(--ink)"></span>
    <span style="background:var(--ink)"></span><span style="background:var(--ink)"></span>
  </div>

  <span class="abs toolbar-label" style="left:371px">Collection</span>
  <div class="abs select" style="left:434px;width:67px">Full<svg width="8" height="5"><path d="M0 0h8L4 5z" fill="#fff"/></svg></div>
  <span class="abs toolbar-label" style="left:637px">Show</span>
  <div class="abs select" style="left:671px;width:69px">12<svg width="8" height="5"><path d="M0 0h8L4 5z" fill="#fff"/></svg></div>
  <span class="abs toolbar-label" style="left:889px">Show</span>
  <div class="abs select" style="left:932px;width:111px">Recommended<svg width="8" height="5"><path d="M0 0h8L4 5z" fill="#fff"/></svg></div>

  <section class="product-grid">
    <article class="abs product" style="left:121px;top:603px"><div class="product-photo" role="img" aria-label="Black sunglasses with grey lenses" style="background:linear-gradient(180deg,#2a2f36,#5b6570)"></div><p class="product-name">Product Name</p><p class="product-price">€ 20</p></article>
    <article class="abs product" style="left:447px;top:603px"><div class="product-photo" role="img" aria-label="Cat-eye sunglasses with purple lenses" style="background:linear-gradient(180deg,#2b1d4a,#8a6cc1)"></div><p class="product-name">Product Name</p><p class="product-price">€ 18</p></article>
    <article class="abs product" style="left:777px;top:603px"><div class="product-photo" role="img" aria-label="Sunglasses with pink gradient lenses" style="background:linear-gradient(180deg,#4a1f33,#e3b8c8)"></div><p class="product-name">Product Name</p><p class="product-price">€ 25</p></article>

    <article class="abs product" style="left:121px;top:898px"><div class="product-photo" role="img" aria-label="Tortoise brown sunglasses with dark lenses" style="background:linear-gradient(180deg,#9a5424,#4a4a40)"></div><p class="product-name">Product Name</p><p class="product-price">€ 25</p></article>
    <article class="abs product" style="left:447px;top:898px"><div class="product-photo" role="img" aria-label="Aviator sunglasses with blue gradient lenses" style="background:linear-gradient(180deg,#2d3d55,#a8b8cc)"></div><p class="product-name">Product Name</p><p class="product-price">€ 20</p></article>
    <article class="abs product" style="left:777px;top:898px"><div class="product-photo" role="img" aria-label="Black cat-eye sunglasses" style="background:linear-gradient(180deg,#151515,#8a8590)"></div><p class="product-name">Product Name</p><p class="product-price">€ 25</p></article>

    <article class="abs product" style="left:121px;top:1196px"><div class="product-photo" role="img" aria-label="Tortoise sunglasses with amber lenses" style="background:linear-gradient(180deg,#5b2c14,#b8754a)"></div><p class="product-name">Product Name</p><p class="product-price">€ 15</p></article>
    <article class="abs product" style="left:447px;top:1196px"><div class="product-photo" role="img" aria-label="Metal frame sunglasses with lilac lenses" style="background:linear-gradient(180deg,#3a3550,#c8c2d6)"></div><p class="product-name">Product Name</p><p class="product-price">€ 20</p></article>
    <article class="abs product" style="left:777px;top:1196px"><div class="product-photo" role="img" aria-label="Brown sunglasses with gradient lenses" style="background:linear-gradient(180deg,#3a2418,#c9b3a0)"></div><p class="product-name">Product Name</p><p class="product-price">€ 20</p></article>

    <article class="abs product" style="left:121px;top:1502px"><div class="product-photo" role="img" aria-label="Black sunglasses with grey lenses" style="background:linear-gradient(180deg,#2a2f36,#5b6570)"></div><p class="product-name">Product Name</p><p class="product-price">€ 25</p></article>
    <article class="abs product" style="left:447px;top:1502px"><div class="product-photo" role="img" aria-label="Navy shield sunglasses with blue lenses" style="background:linear-gradient(180deg,#1b2235,#b8c6d8)"></div><p class="product-name">Product Name</p><p class="product-price">€ 10</p></article>
    <article class="abs product" style="left:777px;top:1502px"><div class="product-photo" role="img" aria-label="Cat-eye sunglasses with purple lenses" style="background:linear-gradient(180deg,#2b1d4a,#8a6cc1)"></div><p class="product-name">Product Name</p><p class="product-price">€ 20</p></article>
  </section>

  <nav class="abs pagination">
    <svg width="8" height="12"><path d="M6 1L1 6l5 5" stroke="#1c1c1c" stroke-width="2" fill="none"/></svg>
    <span class="current">1</span><span>2</span><span>3</span><span>4</span><span>5</span><span>6</span><span>7</span><span>8</span><span>9</span>
    <svg width="8" height="12"><path d="M2 1l5 5-5 5" stroke="#e9b55a" stroke-width="2" fill="none"/></svg>
  </nav>

  <section>
    <div class="abs feature" style="left:165px">
      <svg width="26" height="30" viewBox="0 0 26 30"><circle cx="13" cy="12" r="10" stroke="#e9b55a" stroke-width="2" fill="none"/><path d="M9 24h8M10 28h6" stroke="#e9b55a" stroke-width="2"/></svg>
      <div><h3>Free Shipping</h3><p>Lorem Ipsum is dummy text.</p></div>
    </div>
    <div class="abs feature" style="left:460px">
      <svg width="28" height="30" viewBox="0 0 28 30"><circle cx="14" cy="13" r="11" stroke="#e9b55a" stroke-width="2" fill="none"/><path d="M9 21c2-5 8-5 10 0" stroke="#e9b55a" stroke-width="2" fill="none"/><circle cx="14" cy="11" r="3" fill="#e9b55a"/></svg>
      <div><h3>Premium Support</h3><p>24/7 Customer service</p></div>
    </div>
    <div class="abs feature" style="left:753px">
      <svg width="40" height="28" viewBox="0 0 40 28"><rect x="2" y="4" width="22" height="16" stroke="#e9b55a" stroke-width="2" fill="none"/><path d="M24 9h8l6 6v5H24z" stroke="#e9b55a" stroke-width="2" fill="none"/><circle cx="9" cy="22" r="3" fill="#fff" stroke="#e9b55a" stroke-width="2"/><circle cx="31" cy="22" r="3" fill="#fff" stroke="#e9b55a" stroke-width="2"/></svg>
      <div><h3>Payment Method</h3><p>Cash On Delivery</p></div>
    </div>
  </section>

  <section class="abs brand-band">
    <svg class="abs" style="left:78px;top:62px" width="24" height="40"><path d="M20 2L4 20l16 18" stroke="#1c1c1c" stroke-width="2.5" fill="none"/></svg>
    <svg class="abs" style="left:1101px;top:62px" width="24" height="40"><path d="M4 2l16 18L4 38" stroke="#e9b55a" stroke-width="2.5" fill="none"/></svg>
  </section>
  <span class="abs partner" style="left:232px">Solvane</span>
  <span class="abs partner" style="left:420px">Brivo</span>
  <span class="abs partner" style="left:603px">Linnet</span>
  <span class="abs partner" style="left:782px">Caldor</span>
  <span class="abs partner" style="left:963px">Tessa</span>

  <h2 class="abs newsletter-title">Subscribe For Our Newsletter</h2>
  <div class="abs newsletter-rule"></div>
  <div class="abs email-field">E-Mail Address</div>
  <div class="abs email-submit">
    <svg width="38" height="28" viewBox="0 0 38 28"><path d="M2 2l34 12L2 26l6-12z" stroke="#1c1c1c" stroke-width="2.5" fill="none" stroke-linejoin="round"/><path d="M8 14h28" stroke="#1c1c1c" stroke-width="2.5"/></svg>
  </div>
</main>

<footer class="abs site-footer">
  <div class="abs footer-logo" style="left:161px;top:66px">ORLA</div>
  <p class="abs footer-about" style="left:161px;top:99px">Lorem Ipsum is simply dummy text of the printing and typesetting industry.</p>
  <p class="abs" style="left:161px;top:155px;font-size:11px">READ MORE....</p>
  <div class="abs social" style="left:161px;top:180px;gap:9px">
    <span style="background:var(--accent);width:9px;height:9px"></span><span style="background:var(--accent);width:9px;height:9px"></span><span style="background:var(--accent);width:9px;height:9px"></span><span style="background:var(--accent);width:9px;height:9px"></span><span style="background:var(--accent);width:9px;height:9px"></span>
  </div>

  <h4 class="abs footer-head" style="left:424px;top:82px">QUICK LINK</h4>
  <ul class="abs footer-list" style="left:424px;top:120px">
    <li>Women</li><li>Men</li><li>Youth</li><li>Collections</li><li>Contact Us</li>
  </ul>

  <h4 class="abs footer-head" style="left:635px;top:82px">ACCOUNT</h4>
  <ul class="abs footer-list" style="left:635px;top:120px">
    <li>My Account</li><li>My Wishlist</li><li>Checkout</li><li>Create Account</li><li>Register</li>
  </ul>

  <h4 class="abs footer-head" style="left:860px;top:82px">QUICK CONTACT</h4>
  <div class="abs" style="left:860px;top:120px;font-size:11px;line-height:16.5px">
    <p><svg width="9" height="9" viewBox="0 0 24 24" style="margin-right:8px"><path d="M6.6 10.8a15 15 0 0 0 6.6 6.6l2.2-2.2c.3-.3.7-.4 1-.2 1.1.4 2.3.6 3.6.6.6 0 1 .4 1 1V20c0 .6-.4 1-1 1A17 17 0 0 1 3 4c0-.6.4-1 1-1h3.5c.6 0 1 .4 1 1 0 1.3.2 2.5.6 3.6.1.3 0 .7-.2 1z" fill="#e9b55a"/></svg>+015-482-730-6</p>
    <p style="margin-top:9px"><svg width="10" height="8" viewBox="0 0 10 8" style="margin-right:8px"><rect width="10" height="8" fill="#e9b55a"/><path d="M0 0l5 4 5-4" stroke="#000" fill="none"/></svg>hello@orlaoptics.example</p>
    <p style="margin-top:9px"><svg width="8" height="10" viewBox="0 0 8 10" style="margin-right:10px"><path d="M4 10S0 5.5 0 4a4 4 0 0 1 8 0c0 1.5-4 6-4 6z" fill="#e9b55a"/><circle cx="4" cy="4" r="1.4" fill="#000"/></svg>14 Linden Row</p>
    <p style="padding-left:18px">Harwick Falls, NJ 07412</p>
  </div>

  <div class="abs footer-rule"></div>
  <p class="abs footer-small" style="left:161px">CopyRight ©2018 Orla Eyecare. All Right Reserve</p>
  <p class="abs footer-small" style="left:821px">Privacy Policy - Terms &amp; Conditions</p>
</footer>

</body>
</html>
```